New Business Card Design for Houston-based Office Building Association

We need a business card design for our membership association in Houston known at Houston PELQ (Houston Tower Keepers & Stewards Guild). Our members are office building managers and vendors in the commercial real estate industry. Any building imagery should be of office buildings, skyscrapers, skylines, etc. (Please do NOT use houses or residential homes.) The final design should be clean and cohesive utilizing our logo and branding. I've attached our logos, branding guide, and the information to be included on the business cards.

Target Market(s)

Professionals in office buildings and commercial real estate. Our market is conservative, modern and upmarket.

Contact Information for Business Card

Should include: name, title, email, direct phone number, cell phone number, address, and possibly website. Our address is 4 Larkmoor Court, Suite 300, Houston TX 77021. Our website is houstonpelq.org. Other fields should be editable for each employee.

Colors
ffffff
33b8a4
86cfc6
00a990

Requirements
Must have
• Clean, professional, modern, look, integrating our branding, logo and colors. Our logo font is Gotham Light and signature color is PMS color Pantone 2401C (hex code 40a89d.) Our accent color is PMS color Pantone Cool Gray 10C (hex code: 636466)
Should not have
• NO imagery of homes or residential houses. We represent commercial real estate/office buildings only.

```html
<!DOCTYPE html>
<html lang="en">
<head>
<meta charset="utf-8">
<title>Houston PELQ Business Card</title>
<link rel="stylesheet" href="https://fonts.googleapis.com/css2?family=Montserrat:wght@300;400&display=swap">
<style>
  :root {
    --teal: #40a89d;
    --gray: #636466;
    --paper: #ffffff;
    --stage: #e6e8e8;
  }
  * { box-sizing: border-box; margin: 0; padding: 0; }
  html, body { width: 1200px; height: 880px; overflow: hidden; }
  body {
    background: var(--stage);
    font-family: "Montserrat", Arial, sans-serif;
    font-weight: 300;
    color: var(--gray);
    position: relative;
  }
  .card {
    position: absolute;
    left: 250px;
    width: 700px;
    height: 400px;
    background: var(--paper);
    border-radius: 22px;
    box-shadow: 0 6px 24px rgba(0,0,0,0.12);
  }
  .card--front { top: 30px; }
  .card--back { top: 450px; }

  .wordmark {
    font-weight: 400;
    color: var(--gray);
    white-space: nowrap;
  }

  /* Front */
  .front-name {
    position: absolute;
    left: 0; right: 0; top: 50%;
    transform: translateY(-50%);
    text-align: center;
    font-size: 38px;
    letter-spacing: 0.5px;
  }

  /* Back */
  .back-name {
    position: absolute;
    left: 40px; width: 340px; top: 152px;
    text-align: center;
    font-size: 28px;
  }
  .back-divider {
    position: absolute;
    left: 400px; top: 70px;
    width: 1.5px; height: 200px;
    background: var(--teal);
  }
  .person {
    position: absolute;
    left: 432px; top: 72px;
  }
  .person-name {
    font-size: 21px;
    font-weight: 400;
    letter-spacing: 1px;
    text-transform: uppercase;
    color: var(--gray);
  }
  .person-title {
    font-size: 15px;
    color: var(--teal);
    margin-top: 2px;
  }
  .contact-list {
    list-style: none;
    margin-top: 18px;
  }
  .contact-item {
    display: flex;
    align-items: center;
    gap: 10px;
    font-size: 15px;
    line-height: 1;
    margin-bottom: 9px;
    white-space: nowrap;
  }
  .contact-icon { width: 20px; height: 20px; flex: none; }
  .address {
    position: absolute;
    left: 0; right: 0; bottom: 42px;
    text-align: center;
    font-size: 16px;
    letter-spacing: 0.3px;
    color: var(--gray);
  }
</style>
</head>
<body>

<section class="card card--front" aria-label="Card front">
  <div class="wordmark front-name">Houston PELQ</div>
</section>

<section class="card card--back" aria-label="Card back">
  <div class="wordmark back-name">Houston PELQ</div>

  <span class="back-divider"></span>

  <div class="person">
    <div class="person-name">Dana Whitfield</div>
    <div class="person-title">Owner</div>
    <ul class="contact-list">
      <li class="contact-item">
        <svg class="contact-icon" viewBox="0 0 20 20" aria-hidden="true">
          <circle cx="10" cy="10" r="10" fill="var(--teal)"/>
          <rect x="7" y="4.5" width="6" height="11" rx="1.2" fill="none" stroke="#fff" stroke-width="1.3"/>
        </svg>
        (713) 555-0142
      </li>
      <li class="contact-item">
        <svg class="contact-icon" viewBox="0 0 20 20" aria-hidden="true">
          <circle cx="10" cy="10" r="10" fill="var(--teal)"/>
          <path d="M5 8 Q10 4 15 8 L13.5 9.5 L12 8.5 L8 8.5 L6.5 9.5 Z" fill="#fff"/>
          <rect x="6.5" y="10" width="7" height="4.5" rx="1" fill="#fff"/>
        </svg>
        (713) 555-0187
      </li>
      <li class="contact-item">
        <svg class="contact-icon" viewBox="0 0 20 20" aria-hidden="true">
          <circle cx="10" cy="10" r="10" fill="var(--teal)"/>
          <rect x="5" y="6.5" width="10" height="7" fill="none" stroke="#fff" stroke-width="1.2"/>
          <path d="M5 6.5 L10 10.5 L15 6.5" fill="none" stroke="#fff" stroke-width="1.2"/>
        </svg>
        info@pelqmail.com
      </li>
      <li class="contact-item">
        <svg class="contact-icon" viewBox="0 0 20 20" aria-hidden="true">
          <circle cx="10" cy="10" r="10" fill="var(--teal)"/>
          <circle cx="10" cy="10" r="5" fill="none" stroke="#fff" stroke-width="1.1"/>
          <ellipse cx="10" cy="10" rx="2.2" ry="5" fill="none" stroke="#fff" stroke-width="1"/>
          <line x1="5" y1="10" x2="15" y2="10" stroke="#fff" stroke-width="1"/>
        </svg>
        houstonpelq.org
      </li>
    </ul>
  </div>

  <div class="address">4 Larkmoor Court, Suite 300, Houston TX 77021</div>
</section>

</body>
</html>
```